Brightfield Ventures Inc. Letterhead

Creation of attractive and eye catching letterhead for a business start-up for the construction industry. Letterhead must relate to construction, but avoid standard hammer and tools in the design.

I forgot to add some details, sorry about that. Some pertinent info: Ph: 916-555-0187 brightfieldventures.example 448 Willowmere Ave, Ste 210 Folsom, CA 95999 info@brightfieldventures.example not sure if slogan should be in there" “Connecting construction professionals to create a purpose driven industry.” must be able to be used in word. Thanks!

```html
<!DOCTYPE html>
<html lang="en">
<head>
<meta charset="utf-8">
<title>Brightfield Ventures Inc. Letterhead</title>
<link rel="stylesheet" href="https://fonts.googleapis.com/css2?family=Open+Sans:wght@400;600;700&family=Lato:wght@400;700&display=swap">
<style>
  :root {
    --brand-red: #c0141a;
    --brand-navy: #111a55;
    --ink: #4a4a4a;
    --ink-dark: #333333;
    --paper: #ffffff;
  }
  * { margin: 0; padding: 0; box-sizing: border-box; }
  html, body { width: 1040px; height: 1200px; overflow: hidden; background: var(--paper); }
  .letterhead {
    position: relative;
    width: 1040px;
    height: 1200px;
    background: var(--paper);
    font-family: "Open Sans", Arial, sans-serif;
    color: var(--ink);
  }
  .top-band { position: absolute; top: 0; left: 0; width: 100%; height: 24px; background: var(--brand-red); }
  .brand {
    position: absolute; top: 100px; right: 108px;
    display: flex; flex-direction: column; align-items: flex-end; gap: 14px;
  }
  .brand-line { display: flex; align-items: center; gap: 12px; }
  .brand-mark { width: 22px; height: 22px; background: var(--brand-red); }
  .brand-name {
    font-weight: 700; font-size: 25px; letter-spacing: 0.5px;
    color: var(--brand-navy);
  }
  .brand-slogan {
    font-weight: 600; font-size: 12.5px; letter-spacing: 0.3px;
    color: var(--brand-navy);
    border-top: 2px solid var(--brand-red);
    padding-top: 8px;
  }
  .letter-body {
    position: absolute; left: 99px; top: 215px; width: 840px;
    font-size: 15.5px; line-height: 18px;
  }
  .issue-date { margin-bottom: 18px; }
  .recipient { margin-bottom: 50px; }
  .salutation { margin-bottom: 28px; }
  .paragraph { line-height: 28px; text-align: justify; margin-bottom: 26px; }
  .closing { margin-top: 52px; margin-bottom: 58px; }
  .signer-name { font-size: 19px; color: var(--ink-dark); margin-bottom: 8px; }
  .contact-line {
    position: absolute; left: 0; right: 0; top: 1112px;
    text-align: center; font-family: "Lato", Arial, sans-serif;
    font-size: 17.5px; color: #222;
    white-space: nowrap;
  }
  .contact-line .label { color: var(--brand-red); }
  .contact-line .sep { margin: 0 20px; }
  .contact-line .web { color: var(--brand-red); }
  .footer-band {
    position: absolute; left: 0; bottom: 0; width: 100%; height: 56px;
    background: var(--brand-navy); border-top: 2px solid #3a4487;
    display: flex; align-items: center; justify-content: center;
    font-family: "Lato", Arial, sans-serif; font-size: 17.5px; color: #ffffff;
  }
</style>
</head>
<body>
<main class="letterhead">
  <div class="top-band"></div>

  <header class="brand">
    <div class="brand-line">
      <span class="brand-mark"></span>
      <span class="brand-name">Brightfield Ventures Inc.</span>
    </div>
    <p class="brand-slogan">Connecting construction professionals to create a purpose driven industry.</p>
  </header>

  <section class="letter-body">
    <p class="issue-date">Issuing Date: May 5, 2018</p>
    <p class="recipient">Name Of Employee Mr. XYZABC<br>Address of Employee<br>Address Line 2 etc..</p>
    <p class="salutation">Dear Mr.XYZABC</p>
    <p class="paragraph">Lorem Ipsum has been the industry's standard dummy text ever since the 1500s, when an unknown printer took a galley of type and scrambled it to make a type specimen book. It has survived not only five centuries, but also the leap into electronic typesetting, remaining essentially unchanged. It was popularised in the 1960s with the release of Letraset sheets containing Lorem Ipsum passages, and more recently with desktop publishing software like Aldus PageMaker including versions of Lorem Ipsum.</p>
    <p class="paragraph">Lorem Ipsum is simply dummy text of the printing and typesetting industry. Lorem Ipsum has been the industry's standard dummy text ever since the 1500s, when an unknown printer took a galley of type and scrambled it to make a type specimen book.</p>
    <p class="paragraph">It has survived not only five centuries, but also the leap into electronic typesetting, remaining essentially unchanged. It was popularised in the 1960s with the release of Letraset sheets containing Lorem IpsumIpsum passages.</p>
    <p class="closing">Yours Sincerely</p>
    <p class="signer-name">Dana Whitlow</p>
    <p class="signer-title">Managing Director</p>
  </section>

  <footer>
    <p class="contact-line">
      <span class="label">Ph:</span> 916-555-0187<span class="sep">|</span><span class="label">E:</span> info@brightfieldventures.example<span class="sep">|</span><span class="web">brightfieldventures.example</span>
    </p>
    <div class="footer-band">448 Willowmere Ave, Ste 210, Folsom, CA 95999</div>
  </footer>
</main>
</body>
</html>
```